Chiropractic Business Card

I need a business card designed to help me stand apart from my competition. I really like simple, clean designs that appear open and inviting. I would like the designs to incorporate the color blue, green, or both. I really like the attached picture because it highlights that I just don't treat "back pain" and it being a nice computer graphic helps show that I have a modern practice. "Modern practice" meaning merging technology and most current research in my patient care.

My information is:

Lyle Farwick, DC
Phone- (707) 555-0182
Email- drlylefarwick@mailnest.example
Website- www.brevincourtchiropractic.example
Address- 248 Tolliver Street, Sonoma, CA 95999

Jpeg and pdf attached of Brevincourt Chiropractic logo.
Updates

Atmosphere to be clean lines and solid colors to be have gradient fading, but don't want too much going on with the fading. Simple.

Target Market(s)

Active adults who are health conscious between the ages of 20-70

Industry/Entity Type

Computer

Colors
0455a3
85cae6

Requirements
Must have
• Change color of Brevincourt chiropractic logo (maroon) to fit the rest of the design.
Nice to have
• Can separate the running image from the black background to have it work with the design.

```html
<!DOCTYPE html>
<html lang="en">
<head>
<meta charset="utf-8">
<title>Brevincourt Chiropractic – Business Card</title>
<link rel="stylesheet" href="https://fonts.googleapis.com/css2?family=Orbitron:wght@500;700&display=swap">
<style>
  :root {
    --page-bg: #eceef2;
    --card-bg: #ffffff;
    --navy: #0455a3;
    --navy-soft: #2a74b8;
    --sky: #85cae6;
    --ink: #111827;
    --muted: #2f3a4a;
  }
  * { box-sizing: border-box; margin: 0; padding: 0; }
  html, body {
    width: 1200px; height: 1020px; overflow: hidden;
    background: var(--page-bg);
  }
  .canvas {
    position: relative; width: 1200px; height: 1020px;
    display: flex; align-items: center; justify-content: center;
  }
  .card {
    position: relative; width: 1040px; height: 594px;
    background: var(--card-bg);
    box-shadow: 0 10px 30px rgba(4, 40, 80, 0.18);
    overflow: hidden;
    font-family: "Orbitron", sans-serif;
  }
  .card__chevrons {
    position: absolute; inset: 0; width: 100%; height: 100%;
  }
  .card__info {
    position: absolute; left: 70px; top: 64px; width: 480px;
  }
  .brand {
    display: flex; align-items: center; gap: 16px;
    color: var(--navy);
    font-weight: 700;
    text-transform: uppercase;
    line-height: 1.05;
  }
  .brand__mark {
    width: 54px; height: 54px; flex: none;
    border-radius: 50%;
    background: var(--navy);
  }
  .brand__text { display: flex; flex-direction: column; }
  .brand__name { font-size: 44px; letter-spacing: 1px; }
  .brand__sub { font-size: 14px; letter-spacing: 2.2px; margin-top: 8px; }
  .person { margin-top: 58px; }
  .person__title {
    color: var(--navy);
    font-size: 17px; font-weight: 500; letter-spacing: 3px;
    text-transform: uppercase;
    padding-bottom: 8px;
    border-bottom: 3px solid var(--navy);
    display: block; width: 100%;
  }
  .person__name {
    color: var(--ink);
    font-size: 36px; font-weight: 700; letter-spacing: 1.5px;
    text-transform: uppercase; margin-top: 12px;
    white-space: nowrap;
  }
  .contacts { list-style: none; margin-top: 26px; }
  .contacts__item {
    display: flex; align-items: center; gap: 14px;
    color: var(--muted); font-size: 15px; font-weight: 500;
    margin-bottom: 12px; white-space: nowrap;
  }
  .contacts__icon { width: 20px; height: 20px; flex: none; fill: var(--navy); }
</style>
</head>
<body>
<main class="canvas">
  <article class="card">
    <svg class="card__chevrons" viewBox="0 0 1040 594" preserveAspectRatio="none" aria-hidden="true">
      <defs>
        <linearGradient id="navyFade" x1="0" y1="0" x2="1" y2="1">
          <stop offset="0" stop-color="#0455a3"/>
          <stop offset="1" stop-color="#03498c"/>
        </linearGradient>
      </defs>
      <polygon points="640,0 1040,0 1040,594 640,594 560,297" fill="var(--sky)"/>
      <polygon points="680,0 1040,0 1040,594 680,594 605,297" fill="var(--navy-soft)"/>
      <polygon points="720,0 1040,0 1040,594 720,594 650,297" fill="url(#navyFade)"/>
    </svg>

    <section class="card__info">
      <h1 class="brand">
        <span class="brand__mark"></span>
        <span class="brand__text">
          <span class="brand__name">Brevincourt</span>
          <span class="brand__sub">Chiropractic Offices Inc.</span>
        </span>
      </h1>

      <div class="person">
        <p class="person__title">General Manager</p>
        <h2 class="person__name">Lyle Farwick, DC</h2>
      </div>

      <ul class="contacts">
        <li class="contacts__item">
          <svg class="contacts__icon" viewBox="0 0 24 24"><path d="M6.6 10.8c1.4 2.8 3.8 5.1 6.6 6.6l2.2-2.2c.3-.3.7-.4 1-.2 1.1.4 2.3.6 3.6.6.6 0 1 .4 1 1V20c0 .6-.4 1-1 1C10.6 21 3 13.4 3 4c0-.6.4-1 1-1h3.5c.6 0 1 .4 1 1 0 1.3.2 2.5.6 3.6.1.3 0 .7-.2 1l-2.3 2.2z"/></svg>
          (707) 555-0182
        </li>
        <li class="contacts__item">
          <svg class="contacts__icon" viewBox="0 0 24 24"><path d="M2 5h20v14H2z" fill="none" stroke="var(--navy)" stroke-width="2"/><path d="M2 5l10 8 10-8" fill="none" stroke="var(--navy)" stroke-width="2"/></svg>
          drlylefarwick@mailnest.example
        </li>
        <li class="contacts__item">
          <svg class="contacts__icon" viewBox="0 0 24 24"><g fill="none" stroke="var(--navy)" stroke-width="2"><circle cx="12" cy="12" r="9"/><ellipse cx="12" cy="12" rx="4" ry="9"/><path d="M3 12h18"/></g></svg>
          www.brevincourtchiropractic.example
        </li>
        <li class="contacts__item">
          <svg class="contacts__icon" viewBox="0 0 24 24"><path d="M12 2a7 7 0 0 0-7 7c0 5 7 13 7 13s7-8 7-13a7 7 0 0 0-7-7zm0 9.5A2.5 2.5 0 1 1 12 6.5a2.5 2.5 0 0 1 0 5z"/></svg>
          248 Tolliver Street, Sonoma, CA 95999
        </li>
      </ul>
    </section>
  </article>
</main>
</body>
</html>
```